PSD Designs needed to give to my Developer

Hello, I need PSD files to give to my programmer for the creation of my new website. The website is for KORVA lane, a new clothing company based in Chicago, IL. We sell womens, mens and kids fashion. We specialize in jackets, outerwear and sweaters, but we sell clothing from every category, I have someone working on the logo, so I can't include it for reference. However, I have included 2 reference sites as well as a PDF of how the 2 reference sites could be merged together. The main company color should be blue (hence the name KORVA lane), and the overall feel of the site should be FUN. It should communicate: This is where you want to shop if you want a FUN, HAPPY experience. I need the Home Page file designed very quickly. Whoever is awarded this job will immediately continue working with me to design the other 8 pages. I will pay for all pages. The amount I am offering is for this one page only, and I will pay you additional to design all other 8 pages. Thank you for your time and I will be picking the best design so that we can immediately build a great relationship and work through the rest of the project.

Industry/Entity Type

Apparel Store

Number of Pages Required

1 page

Font styles to use
Sans Serif

Colors
33a6d7
0492cd
ffffff

Requirements
Must have
• I have included all notes in the project description so please check there. My project must communicate: Fun and Happy Design. Even tho I have chosen a few variations of blue below, I still want the designer to incorporate other colors as necessary to acheive the desired look.
Should not have
• It should have a boring, childish feel

```html
<!DOCTYPE html>
<html lang="en">
<head>
<meta charset="UTF-8">
<title>KORVA lane — Home</title>
<link href="https://fonts.googleapis.com/css2?family=Poppins:wght@400;500;600;800&family=Raleway:wght@500;600;700&display=swap" rel="stylesheet">
<style>
  :root {
    --blue: #1480c4;
    --blue-deep: #0d72b3;
    --ink: #1b1b1b;
    --paper: #f2f1ef;
    --topbar: #e8e8e8;
    --footer: #1f1f1f;
    --white: #ffffff;
  }
  * { box-sizing: border-box; margin: 0; padding: 0; }
  html, body { width: 1173px; height: 1200px; overflow: hidden; background: var(--white); }
  body { position: relative; font-family: "Raleway", sans-serif; color: var(--ink); }

  .topbar { position: absolute; left: 0; top: 0; width: 1173px; height: 49px; background: var(--topbar); }
  .topbar__promo { position: absolute; left: 96px; top: 16px; font-size: 12.5px; font-weight: 600; }
  .topbar__arrow { position: absolute; left: 931px; top: 14px; }
  .login { position: absolute; left: 987px; top: 9px; width: 89px; height: 31px; border: 1.5px solid #222; border-radius: 16px;
    display: flex; align-items: center; justify-content: center; gap: 8px; font-size: 13px; font-weight: 600; }

  .nav { position: absolute; left: 0; top: 49px; width: 1173px; height: 69px; background: var(--blue); }
  .nav__item { position: absolute; top: 28px; color: var(--white); font-size: 12px; font-weight: 700; letter-spacing: .1px; }
  .nav__item--active::after { content: ""; position: absolute; left: 1px; right: 1px; top: 38px; height: 3px; background: var(--white); }
  .brand { position: absolute; right: 97px; top: 18px; color: var(--white); font-size: 27px; font-weight: 600; }

  .hero { position: absolute; left: 0; top: 118px; width: 1173px; height: 459px; background: var(--paper); }
  .hero__photo { position: absolute; left: 21px; top: 8px; width: 373px; height: 451px;
    background: linear-gradient(180deg, #ecebe9 0%, #b9875a 35%, #a7713f 70%, #e8e6e3 100%); }
  .hero__frame { position: absolute; left: 367px; top: 75px; width: 582px; height: 311px; border: 5px solid var(--blue); text-align: center; }
  .hero__title { font-family: "Poppins", sans-serif; line-height: 1.2; margin-top: 68px; }
  .hero__title .strong { font-weight: 800; }
  .hero__l1 { font-size: 38px; display: block; }
  .hero__l2 { font-size: 41px; display: block; font-weight: 400; }
  .hero__l3 { font-size: 41px; display: block; font-weight: 400; margin-top: 4px; }
  .shop-badge { position: absolute; left: 341px; top: 260px; width: 154px; height: 154px; border-radius: 50%; background: var(--blue);
    display: flex; align-items: center; justify-content: center; color: var(--white); font-family: "Poppins", sans-serif; font-size: 15px; font-weight: 500; }
  .shop-badge::before { content: ""; position: absolute; inset: 10px; border: 2px dotted rgba(255,255,255,.9); border-radius: 50%; }
  .dots { position: absolute; left: 551px; top: 426px; display: flex; gap: 10px; }
  .dots span { width: 10px; height: 10px; border-radius: 50%; background: var(--blue); border: 2px solid var(--blue); }
  .dots .off { background: var(--white); }

  .tile { position: absolute; overflow: hidden; }
  .tile__label { position: absolute; font-family: "Poppins", sans-serif; font-weight: 600; line-height: 1.15; }
  .tile--story { left: 0; top: 587px; width: 463px; height: 508px; background: linear-gradient(135deg, #e9e6ea 0%, #f0e3e4 45%, #e6b6c4 75%, #d64a78 100%); }
  .tile--story .tile__label { left: 176px; top: 50px; font-size: 48px; color: #222; }
  .tile--shop { left: 473px; top: 587px; width: 700px; height: 249px; background: linear-gradient(180deg, #4c5056 0%, #6b7076 55%, #9a9da2 100%); }
  .tile--shop .tile__label { left: 12px; top: 90px; font-size: 50px; color: var(--white); text-shadow: 0 2px 4px rgba(0,0,0,.4); }
  .tile--movement { left: 473px; top: 846px; width: 700px; height: 249px; background: linear-gradient(180deg, #2f4f55 0%, #5d7d4f 45%, #98a954 100%); }
  .tile--movement .tile__label { left: 32px; top: 82px; font-size: 33px; color: var(--white); text-shadow: 0 2px 4px rgba(0,0,0,.4); }

  .footer { position: absolute; left: 0; top: 1104px; width: 1173px; height: 96px; background: var(--footer); color: var(--white); text-align: center; font-size: 12.5px; font-weight: 500; }
  .footer p:first-child { margin-top: 26px; }
  .footer p + p { margin-top: 10px; }
</style>
</head>
<body>
  <header class="topbar">
    <p class="topbar__promo">Pop-up your own KORVA Boulevard for ONLY $99</p>
    <svg class="topbar__arrow" width="40" height="22" viewBox="0 0 40 22" aria-hidden="true">
      <path d="M2 4 C2 16 20 20 36 8" fill="none" stroke="#222" stroke-width="1.6"/>
      <path d="M28 6 L37 7 L34 15" fill="none" stroke="#222" stroke-width="1.6"/>
    </svg>
    <a class="login">
      <svg width="9" height="11" viewBox="0 0 9 11" aria-hidden="true"><rect x="0" y="4.5" width="9" height="6.5" rx="1" fill="#222"/><path d="M2 5V3a2.5 2.5 0 0 1 5 0v2" fill="none" stroke="#222" stroke-width="1.5"/></svg>
      Login
    </a>
  </header>

  <nav class="nav">
    <a class="nav__item nav__item--active" style="left:96px">HOME</a>
    <a class="nav__item" style="left:181px">GET TO KNOW US</a>
    <a class="nav__item" style="left:338px">WHY KORVA?</a>
    <a class="nav__item" style="left:452px">HOST A POP-UP</a>
    <a class="nav__item" style="left:597px">BECOME A STYLIST</a>
    <span class="brand">KORVA lane</span>
  </nav>

  <section class="hero">
    <div class="hero__photo" role="img" aria-label="Man in a tan suede bomber jacket and glasses"></div>
    <div class="hero__frame">
      <h1 class="hero__title">
        <span class="hero__l1 strong">LIMITED INVENTORY</span>
        <span class="hero__l2">that’s only available for</span>
        <span class="hero__l3"><span class="strong">ONE</span> Week!</span>
      </h1>
    </div>
    <a class="shop-badge">SHOP NOW</a>
    <div class="dots"><span></span><span></span><span class="off"></span><span></span></div>
  </section>

  <a class="tile tile--story" role="img" aria-label="Smiling woman holding shopping bags near a clothing rack">
    <span class="tile__label">Our Story</span>
  </a>
  <a class="tile tile--shop" role="img" aria-label="Six women modelling coats and jackets">
    <span class="tile__label">Shop</span>
  </a>
  <a class="tile tile--movement" role="img" aria-label="Two happy children in blue hoodies sitting outdoors">
    <span class="tile__label">Be Happier,<br>Join the Movement</span>
  </a>

  <footer class="footer">
    <p>Copyright © 2018 KORVA lane . All rights reserved.</p>
    <p>Terms &amp; Conditions | Privacy Policy</p>
  </footer>
</body>
</html>
```